New Business Card Design for Manufacturing

We are an engineering/manufacturing company that offers Advanced machining/assembly/engineering services, as well as innovative products for the heavy duty engine cooling markets.

We are looking to get a new business card designed that is clean and modern looking, but still fits the wide range of technical/skilled work we do.

- We hope to use this design as the base for other design work in new Presentations, web, and print work.

Industry/Entity Type

Engineering

Contact Information for Business Card

Our preferred color of blue is (RGB) 22/71/159 but can vary slightly from that color. Our content will be our Logo and full company name (Vantrell Forge Works, Inc.), company address, name, job title, phone number with extension, cell number, fax number, website, and email address on the cards.
We'd like the full company name next to the logo, but we are open to other interpretations of that layout.
Preferably, we would like the back side to be clean with just our logo, and the front to contain all of the contact information.

Colors
2f74b4
0355a3
85abd2

Requirements
Must have
• - Logo, company name, needed content - We are open to interpretation beyond that.
• - Standard size business card.
• - Horizontal orientation.
• - Enough space for lengthy names / job titles (for example, a job title could read "Directory of Human Resources" or "V.P. of Governmental Affairs"). We need this to look clean, whether the title be short (CEO) or long (as described above).

```html
<!DOCTYPE html>
<html lang="en">
<head>
<meta charset="utf-8">
<title>Vantrell Forge Works – Business Card</title>
<link rel="stylesheet" href="https://fonts.googleapis.com/css2?family=Fira+Sans:wght@500;600&family=Open+Sans:wght@400;600&display=swap">
<style>
  :root {
    --brand-blue: #02549a;
    --brand-blue-deep: #004a8c;
    --accent-blue: #2f74b4;
    --steel-gray: #7d8389;
    --ink: #333a40;
    --card-white: #f7f7f7;
    --backdrop: #e9e9e9;
  }
  * { box-sizing: border-box; margin: 0; padding: 0; }
  html, body { width: 1200px; height: 576px; overflow: hidden; }
  body {
    background: var(--backdrop);
    position: relative;
    font-family: "Open Sans", sans-serif;
    color: var(--ink);
  }
  .card {
    position: absolute;
    top: 138px;
    width: 484px;
    height: 294px;
    border-radius: 13px;
    overflow: hidden;
  }

  /* Back side */
  .card-back {
    left: 82px;
    background: linear-gradient(180deg, var(--brand-blue) 0%, var(--brand-blue-deep) 100%);
    color: #fff;
  }
  .card-back .wordmark {
    position: absolute;
    left: 0; right: 0; top: 92px;
    text-align: center;
    font-family: "Fira Sans", sans-serif;
    font-weight: 600;
    font-size: 66px;
    line-height: 1;
    letter-spacing: 1px;
    color: #fff;
  }
  .card-back .tagline {
    position: absolute;
    left: 0; right: 0; top: 172px;
    text-align: center;
    font-family: "Fira Sans", sans-serif;
    font-weight: 600;
    font-size: 17px;
    letter-spacing: 1px;
  }
  .card-back .site-line {
    position: absolute;
    left: 0; right: 0; top: 266px;
    display: flex;
    justify-content: center;
    align-items: center;
    gap: 12px;
    font-size: 12.5px;
  }
  .card-back .site-line .rule {
    width: 54px; height: 2px;
    background: linear-gradient(90deg, transparent, #fff 50%, transparent);
  }

  /* Front side */
  .card-front {
    left: 602px;
    width: 481px;
    background: var(--card-white);
  }
  .card-front .edge-dot {
    position: absolute;
    left: -14px; top: 53px;
    width: 22px; height: 42px;
    border-radius: 0 21px 21px 0;
    background: var(--brand-blue);
  }
  .card-front .person-name {
    position: absolute;
    left: 22px; top: 34px;
    font-family: "Fira Sans", sans-serif;
    font-weight: 500;
    font-size: 21px;
    color: var(--brand-blue);
  }
  .card-front .person-title {
    position: absolute;
    left: 22px; top: 63px;
    font-size: 11.5px;
  }
  .card-front .wordmark {
    position: absolute;
    right: 20px; top: 28px;
    font-family: "Fira Sans", sans-serif;
    font-weight: 600;
    font-size: 44px;
    line-height: 1;
    color: var(--brand-blue);
  }
  .card-front .tagline {
    position: absolute;
    right: 26px; top: 82px;
    font-family: "Fira Sans", sans-serif;
    font-weight: 600;
    font-size: 12px;
    letter-spacing: 0.5px;
    color: var(--steel-gray);
  }
  .card-front .company-name {
    position: absolute;
    left: 22px; top: 119px;
    font-family: "Fira Sans", sans-serif;
    font-weight: 500;
    font-size: 14.5px;
    color: var(--brand-blue);
  }
  .contact-list {
    position: absolute;
    left: 22px; top: 144px;
    list-style: none;
    font-size: 12px;
    line-height: 17.4px;
  }
  .contact-list li { display: flex; align-items: center; gap: 8px; }
  .contact-list svg { width: 11px; height: 11px; fill: var(--brand-blue); flex: none; }
  .contact-list .site-domain { color: var(--brand-blue); }
  .card-front .wave { position: absolute; left: 0; top: 0; width: 481px; height: 294px; }
  .card-front .address {
    position: absolute;
    right: 20px; top: 232px;
    text-align: right;
    font-size: 12px;
    line-height: 17px;
    color: #fff;
  }
</style>
</head>
<body>

  <section class="card card-back" aria-label="Card back">
    <div class="wordmark">VANTRELL</div>
    <div class="tagline">BUILT TO ENDURE</div>
    <div class="site-line"><span class="rule"></span><span>www.vantrellforge.com</span><span class="rule"></span></div>
  </section>

  <section class="card card-front" aria-label="Card front">
    <svg class="wave" viewBox="0 0 481 294" aria-hidden="true">
      <path fill="var(--steel-gray)" d="M0,232 C130,286 270,242 350,202 C410,174 450,176 481,178 L481,187 C450,185 405,188 348,212 C265,248 130,290 0,244 Z"/>
      <path fill="var(--brand-blue)" d="M0,252 C130,300 275,258 352,220 C410,192 452,190 481,192 L481,294 L0,294 Z"/>
    </svg>
    <span class="edge-dot"></span>
    <h1 class="person-name">Jordan Ellis Marsh</h1>
    <p class="person-title">Managing Director</p>
    <div class="wordmark">VANTRELL</div>
    <div class="tagline">BUILT TO ENDURE</div>
    <h2 class="company-name">Vantrell Forge Works, Inc.</h2>
    <ul class="contact-list">
      <li><svg viewBox="0 0 12 12"><path d="M1 4c0-2 2-3 5-3s5 1 5 3v1H8.5V3.6h-5V5H1zM2.5 6h7l1 5h-9z"/></svg>111-2222-2222 (EXT)</li>
      <li><svg viewBox="0 0 12 12"><path d="M3 0h6a1 1 0 0 1 1 1v10a1 1 0 0 1-1 1H3a1 1 0 0 1-1-1V1a1 1 0 0 1 1-1zm0 2v7h6V2z"/></svg>333-3333-3333</li>
      <li><svg viewBox="0 0 12 12"><path d="M3 0h6v3H3zM0 4h12v5H10v3H2V9H0zm3 4v3h6V8z"/></svg>444-4444-4444</li>
      <li><svg viewBox="0 0 12 12"><path d="M0 2h12v8H0zm1 1v.5l5 3.5 5-3.5V3z"/></svg>jmarsh@vantrellforge.com</li>
      <li><svg viewBox="0 0 12 12"><path d="M6 0a6 6 0 1 0 0 12A6 6 0 0 0 6 0zM1.1 5.3h2.4c.1-1.6.5-3 1.1-3.9A5 5 0 0 0 1.1 5.3zm0 1.4a5 5 0 0 0 3.5 3.9c-.6-.9-1-2.3-1.1-3.9zm3.8 0c.1 2 .7 3.7 1.1 4 .4-.3 1-2 1.1-4zm0-1.4h2.2c-.1-2-.7-3.7-1.1-4-.4.3-1 2-1.1 4zm3.6 0h2.4a5 5 0 0 0-3.5-3.9c.6.9 1 2.3 1.1 3.9zm0 1.4c-.1 1.6-.5 3-1.1 3.9a5 5 0 0 0 3.5-3.9z"/></svg>www.<span class="site-domain">vantrellforge</span>.com</li>
    </ul>
    <address class="address" style="font-style:normal">518 Millrace Rd., Dorrick,<br>Any Town, US 246810</address>
  </section>

</body>
</html>
```